Urkunden
Zielgruppe
www.jolbertrasmund.example
www.vitalschwung.example
Aufgabenstellung
Ich bräuchte Urkunden für vier Kategorien einer Marke. Dem Vital Schwung, dass ich bis dato zusammen mit einer Geschäftspartnerin geführt habe. Jetzt gehen wir getrennte Wege.
Unter http://www.vitalschwung.example/de/about-me0/ findet man die Titel, die in der Ausbildung erreicht werden können.
VSg Practitioner, VSg Master Practitioner
VSg Coach und VSg Master Coach
Die Urkunden sollten in Ihrer Aufmachung mit steigendem Titel pompöser und Aussagestärker werden.
Das Vital Schwung ist eine Art energetischer Werkzeugkasten, den ich unterrichte.
Wichtig ist, es soll damit auch "Jobst Rasmund" in den Vordergrund gerückt werden, der Urkunden für das Erlernte "Werkzeug" heraus gibt: "Vital Schwung"

```html
<!DOCTYPE html>
<html lang="de">
<head>
<meta charset="utf-8">
<title>Urkunden – Vital Schwung</title>
<link rel="stylesheet" href="https://fonts.googleapis.com/css2?family=Libre+Baskerville:wght@400;700&family=Dosis:wght@300;500&display=swap">
<style>
  :root {
    --bg: #e9e6e0;
    --paper: #fcfaf4;
    --ink: #3c3a3b;
    --ink-soft: #5a5858;
    --dark: #1f1f1f;
    --dark-warm: #454143;
    --gold-1: #d9a917;
    --gold-2: #f6d866;
    --rule: #b9b7b3;
  }
  * { box-sizing: border-box; margin: 0; padding: 0; }
  html, body { width: 1200px; height: 1050px; overflow: hidden; }
  body {
    background: var(--bg);
    display: flex;
    align-items: center;
    justify-content: center;
    gap: 28px;
    font-family: "Libre Baskerville", Georgia, serif;
    color: var(--ink);
  }
  .certificate {
    position: relative;
    width: 265px;
    height: 372px;
    background: var(--paper);
    box-shadow: 0 6px 18px rgba(0,0,0,.22);
    overflow: hidden;
  }
  .certificate__header {
    position: absolute;
    top: 0; left: 0;
    width: 265px; height: 110px;
  }
  .certificate__seal {
    position: absolute;
    left: 50%;
    top: 12px;
    width: 64px; height: 64px;
    margin-left: -32px;
    border-radius: 50%;
  }
  .certificate__seal--silver { background: radial-gradient(circle at 40% 35%, #f2f2f2, #a8a8a8 60%, #7a7a7a); }
  .certificate__seal--gold { background: radial-gradient(circle at 40% 35%, #fff1a8, #f1c93a 55%, #d6a413); }
  .certificate__title {
    position: absolute;
    top: 124px; left: 0; right: 0;
    text-align: center;
    font-weight: 700;
    font-size: 33px;
    letter-spacing: .5px;
    line-height: 1;
  }
  .certificate__level {
    position: absolute;
    top: 162px; left: 50%;
    transform: translateX(-50%);
    white-space: nowrap;
    padding: 3px 5px 2px;
    font-weight: 700;
    text-transform: uppercase;
    color: #fff;
    line-height: 1.1;
  }
  .certificate__level--silver { background: linear-gradient(90deg, var(--dark) 0%, #555 55%, #aaa 100%); font-size: 15px; }
  .certificate__level--gold { background: linear-gradient(90deg, var(--gold-1), var(--gold-2) 55%, var(--gold-1)); }
  .certificate__level--small { font-size: 11.5px; padding: 4px 4px 3px; }
  .certificate__level--large { font-size: 18px; }
  .certificate__level--medium { font-size: 14.5px; padding: 3px 7px 2px; }
  .certificate__by {
    position: absolute;
    top: 204px; left: 0; right: 0;
    text-align: center;
    font-size: 8px;
    color: var(--ink);
  }
  .certificate__issuer {
    position: absolute;
    top: 218px; left: 0; right: 0;
    text-align: center;
    font-family: "Dosis", sans-serif;
    font-weight: 500;
    font-size: 14px;
    letter-spacing: .3px;
    color: var(--ink-soft);
    white-space: nowrap;
  }
  .certificate__to {
    position: absolute;
    top: 245px; left: 0; right: 0;
    text-align: center;
    font-size: 7px;
    color: var(--ink);
  }
  .certificate__recipient {
    position: absolute;
    top: 266px; left: 52px; right: 52px;
    text-align: center;
    font-family: "Dosis", sans-serif;
    font-weight: 300;
    font-size: 17px;
    color: var(--ink);
    border-bottom: 1px solid var(--rule);
    padding-bottom: 1px;
  }
  .certificate__signatures {
    position: absolute;
    top: 334px; left: 14px; right: 18px;
    display: flex;
    justify-content: space-between;
  }
  .certificate__sign {
    width: 80px;
    border-top: 1px solid var(--rule);
    text-align: center;
    font-size: 4px;
    padding-top: 3px;
    color: var(--ink-soft);
  }
  .certificate__footer {
    position: absolute;
    left: 0; right: 0; bottom: 0;
  }
  .certificate__footer--silver {
    height: 10px;
    bottom: 4px;
    background: linear-gradient(90deg, #2a2a2a, #888 55%, #ddd);
  }
  .certificate__footer--gold {
    height: 14px;
    background: linear-gradient(180deg, var(--gold-2) 0, var(--gold-1) 6px, var(--paper) 6px, var(--paper) 7px, var(--dark-warm) 7px);
  }
</style>
</head>
<body>

<article class="certificate">
  <svg class="certificate__header" viewBox="0 0 265 110" preserveAspectRatio="none" aria-hidden="true">
    <defs>
      <linearGradient id="silverBand" x1="0" x2="1">
        <stop offset="0" stop-color="#2e2e2e"/><stop offset=".5" stop-color="#bdbdbd"/><stop offset="1" stop-color="#e6e6e6"/>
      </linearGradient>
    </defs>
    <polygon points="0,0 265,0 265,82 132.5,48 0,82" fill="var(--dark)"/>
    <polygon points="0,82 132.5,48 265,82 265,104 132.5,64 0,104" fill="url(#silverBand)"/>
  </svg>
  <div class="certificate__seal certificate__seal--silver" role="img" aria-label="Silbernes Siegel mit Stern und Lorbeerkranz"></div>
  <h1 class="certificate__title">URKUNDE</h1>
  <p class="certificate__level certificate__level--silver">VSg Practitioner</p>
  <p class="certificate__by">verliehen durch</p>
  <p class="certificate__issuer">jobstrasmund</p>
  <p class="certificate__to">an</p>
  <p class="certificate__recipient">Lena Hartwig</p>
  <div class="certificate__signatures">
    <span class="certificate__sign">Ort, Datum</span>
    <span class="certificate__sign">Jobst Rasmund</span>
  </div>
</article>

<article class="certificate">
  <svg class="certificate__header" viewBox="0 0 265 110" preserveAspectRatio="none" aria-hidden="true">
    <defs>
      <linearGradient id="silverBand2" x1="0" x2="1">
        <stop offset="0" stop-color="#2e2e2e"/><stop offset=".5" stop-color="#bdbdbd"/><stop offset="1" stop-color="#e6e6e6"/>
      </linearGradient>
    </defs>
    <polygon points="0,0 265,0 265,82 132.5,48 0,82" fill="var(--dark)"/>
    <polygon points="0,82 132.5,48 265,82 265,104 132.5,64 0,104" fill="url(#silverBand2)"/>
  </svg>
  <div class="certificate__seal certificate__seal--gold" role="img" aria-label="Goldenes Siegel mit zwei Sternen und Lorbeerkranz"></div>
  <h1 class="certificate__title">URKUNDE</h1>
  <p class="certificate__level certificate__level--gold certificate__level--small">VSg Master Practitioner</p>
  <p class="certificate__by">verliehen durch</p>
  <p class="certificate__issuer">jobstrasmund</p>
  <p class="certificate__to">an</p>
  <p class="certificate__recipient">Lena Hartwig</p>
  <div class="certificate__signatures">
    <span class="certificate__sign">Ort, Datum</span>
    <span class="certificate__sign">Jobst Rasmund</span>
  </div>
</article>

<article class="certificate">
  <svg class="certificate__header" viewBox="0 0 265 110" preserveAspectRatio="none" aria-hidden="true">
    <defs>
      <linearGradient id="silverBand3" x1="0" x2="1">
        <stop offset="0" stop-color="#2e2e2e"/><stop offset=".5" stop-color="#bdbdbd"/><stop offset="1" stop-color="#e6e6e6"/>
      </linearGradient>
    </defs>
    <polygon points="0,0 265,0 265,82 132.5,48 0,82" fill="var(--dark)"/>
    <polygon points="0,82 132.5,48 265,82 265,104 132.5,64 0,104" fill="url(#silverBand3)"/>
  </svg>
  <div class="certificate__seal certificate__seal--gold" role="img" aria-label="Goldenes Siegel mit drei Sternen und Lorbeerkranz"></div>
  <h1 class="certificate__title">URKUNDE</h1>
  <p class="certificate__level certificate__level--gold certificate__level--large">VSg Coach</p>
  <p class="certificate__by">verliehen durch</p>
  <p class="certificate__issuer">jobstrasmund</p>
  <p class="certificate__to">an</p>
  <p class="certificate__recipient">Lena Hartwig</p>
  <div class="certificate__signatures">
    <span class="certificate__sign">Ort, Datum</span>
    <span class="certificate__sign">Jobst Rasmund</span>
  </div>
  <div class="certificate__footer certificate__footer--silver"></div>
</article>

<article class="certificate">
  <svg class="certificate__header" viewBox="0 0 265 110" preserveAspectRatio="none" aria-hidden="true">
    <defs>
      <linearGradient id="goldBand" x1="0" x2="1">
        <stop offset="0" stop-color="#f3cd45"/><stop offset=".5" stop-color="#f8e08a"/><stop offset="1" stop-color="#dcaa16"/>
      </linearGradient>
    </defs>
    <polygon points="0,0 265,0 265,82 132.5,48 0,82" fill="var(--dark-warm)"/>
    <polygon points="0,82 132.5,48 265,82 265,100 132.5,64 0,100" fill="url(#goldBand)"/>
  </svg>
  <div class="certificate__seal certificate__seal--gold" role="img" aria-label="Goldenes Siegel mit vier Sternen und Lorbeerkranz"></div>
  <h1 class="certificate__title">URKUNDE</h1>
  <p class="certificate__level certificate__level--gold certificate__level--medium">VSg Master Coach</p>
  <p class="certificate__by">verliehen durch</p>
  <p class="certificate__issuer">jobstrasmund</p>
  <p class="certificate__to">an</p>
  <p class="certificate__recipient">Lena Hartwig</p>
  <div class="certificate__signatures">
    <span class="certificate__sign">Ort, Datum</span>
    <span class="certificate__sign">Jobst Rasmund</span>
  </div>
  <div class="certificate__footer certificate__footer--gold"></div>
</article>

</body>
</html>
```